Homemaking training schools needs a Business Card design

Designer, Hello!

No special requirements, good-looking enough.
--------------------------------------------------------------------------

Name: Marcus Dole
Chairman
Tel: 0574-71948263
Mobile: 13857420916
Email: kelvora@mailnest.example
Web: www.prt2019.example
Add: No.258, LanpingJie, BeiyuanQu, Ningbo, Zhejiang

LOGO
Ningbo PRT Homemaking Training School

Target Market(s)

pregnant women, mothers, infants, the elderly and families, including cleaning, cooking, nursing training.

Industry/Entity Type

Business

Contact Information for Business Card

Name: Marcus Dole
Chairman
Tel: 0574-71948263
Mobile: 13857420916
Email: kelvora@mailnest.example
Web: www.prt2019.example

LOGO

Font styles to use
Serif
Sans Serif
Decorative

Requirements
Nice to have
• Feels: clean, specifications, safety, comfort, warmth and happiness.

```html
<!DOCTYPE html>
<html lang="en">
<head>
<meta charset="utf-8">
<title>PeiRuiTang Business Card</title>
<link rel="stylesheet" href="https://fonts.googleapis.com/css2?family=Lato:wght@400;700&family=Quicksand:wght@500;700&display=swap">
<style>
  :root {
    --brand-blue: #3a78bb;
    --brand-magenta: #c8188f;
    --paper: #ffffff;
    --stage: #e9ebee;
    --ink-light: #ffffff;
    --ink-dark: #2b2b2b;
  }
  * { margin: 0; padding: 0; box-sizing: border-box; }
  html, body { width: 1200px; height: 900px; overflow: hidden; }
  body {
    background: var(--stage);
    font-family: "Lato", sans-serif;
    display: flex;
    flex-direction: column;
    align-items: center;
    justify-content: center;
    gap: 40px;
  }
  .card {
    position: relative;
    width: 665px;
    height: 380px;
    overflow: hidden;
    box-shadow: 0 6px 18px rgba(0,0,0,0.18);
  }
  .card-back { background: var(--brand-blue); color: var(--ink-light); }
  .card-front { background: var(--paper); }

  .wordmark {
    font-family: "Quicksand", sans-serif;
    font-weight: 700;
    letter-spacing: -0.5px;
    white-space: nowrap;
  }
  .tagline {
    display: flex;
    align-items: center;
    gap: 10px;
    font-family: "Quicksand", sans-serif;
    font-weight: 500;
    white-space: nowrap;
  }
  .tagline::before, .tagline::after {
    content: ""; height: 1.5px; background: currentColor; flex: 1;
  }

  /* back */
  .back-brand {
    position: absolute; left: 0; right: 0; top: 110px;
    display: flex; flex-direction: column; align-items: center;
  }
  .back-brand .wordmark { font-size: 66px; color: var(--ink-light); }
  .back-brand .tagline { width: 480px; font-size: 20px; margin-top: 6px; }
  .back-url { margin-top: 26px; font-size: 17px; letter-spacing: 3px; }

  /* front */
  .front-shapes { position: absolute; inset: 0; }
  .front-brand {
    position: absolute; left: 18px; top: 128px; width: 270px;
    display: flex; flex-direction: column; align-items: center;
    color: var(--brand-blue);
  }
  .front-brand .wordmark { font-size: 42px; }
  .front-brand .tagline { width: 270px; font-size: 15px; color: var(--ink-dark); margin-top: 4px; }

  .contact {
    position: absolute; left: 410px; top: 72px; right: 16px;
    color: var(--ink-light);
  }
  .contact-name { font-size: 28px; font-weight: 700; }
  .contact-title { font-size: 16px; color: var(--brand-magenta); margin-top: 2px; font-weight: 700; }
  .contact-address { font-size: 16px; line-height: 1.35; margin-top: 14px; }
  .contact-list { list-style: none; margin-top: 12px; }
  .contact-list li {
    display: flex; align-items: center; gap: 10px;
    font-size: 17px; line-height: 1.55; white-space: nowrap;
  }
  .contact-list svg { width: 14px; height: 14px; flex: none; }
</style>
</head>
<body>

  <section class="card card-back">
    <div class="back-brand">
      <div class="wordmark">PeiRuiTang</div>
      <div class="tagline">Training &amp; Services</div>
      <div class="back-url">www.prt2019.example</div>
    </div>
  </section>

  <section class="card card-front">
    <svg class="front-shapes" viewBox="0 0 665 380" width="665" height="380">
      <path d="M352,0 C346,150 300,270 195,345 C285,280 330,160 340,0 Z" fill="var(--brand-blue)"/>
      <path d="M372,0 C366,170 320,300 225,380 L262,380 C335,300 378,170 388,0 Z" fill="var(--brand-magenta)"/>
      <path d="M388,0 L665,0 L665,380 L262,380 C335,300 378,170 388,0 Z" fill="var(--brand-blue)"/>
    </svg>

    <div class="front-brand">
      <div class="wordmark">PeiRuiTang</div>
      <div class="tagline">Training &amp; Services</div>
    </div>

    <div class="contact">
      <div class="contact-name">Marcus Dole</div>
      <div class="contact-title">Chairman</div>
      <div class="contact-address">No.258, LanpingJie<br>BeiyuanQu, Ningbo, Zhejiang</div>
      <ul class="contact-list">
        <li>
          <svg viewBox="0 0 16 16"><path d="M3 1 L6 1 L7 5 L5 6.5 C6 9 7 10 9.5 11 L11 9 L15 10 L15 13 C15 14 14 15 13 15 C6 15 1 10 1 3 C1 2 2 1 3 1 Z" fill="var(--brand-magenta)"/></svg>
          0574-71948263
        </li>
        <li>
          <svg viewBox="0 0 16 16"><rect x="4" y="1" width="8" height="14" rx="1.5" fill="none" stroke="var(--brand-magenta)" stroke-width="1.6"/><circle cx="8" cy="12.5" r="0.9" fill="var(--brand-magenta)"/></svg>
          1385-7420916
        </li>
        <li>
          <svg viewBox="0 0 16 16"><rect x="1" y="3" width="14" height="10" fill="var(--brand-magenta)"/><path d="M1 3 L8 9 L15 3" fill="none" stroke="var(--brand-blue)" stroke-width="1.3"/></svg>
          kelvora@mailnest.example
        </li>
        <li>
          <svg viewBox="0 0 16 16"><circle cx="8" cy="8" r="6.5" fill="none" stroke="var(--brand-magenta)" stroke-width="1.5"/><ellipse cx="8" cy="8" rx="2.8" ry="6.5" fill="none" stroke="var(--brand-magenta)" stroke-width="1.2"/><path d="M1.5 8 H14.5" stroke="var(--brand-magenta)" stroke-width="1.2"/></svg>
          www.prt2019.example
        </li>
      </ul>
    </div>
  </section>

</body>
</html>
```